Wordpress - For IT, Cloud/Hosting, Residential/Commercial Construction Services

We are a holding company for service companies. We want the current Wordpress site modified or a new wordpress site completed. We want this site to be the parent website, that then has pull down menus linking to our other website (currently http://brightwallfix.com, http://q7v.host and would like it to be easy and fluid as we acquire more companies as we have with TKLS, Inc., B&J Construction, Brightwall Fix etc. Model after sites like Pemrose.com, Tallowbine.com, QDV.com,.vanterelm.com

------

The parent is the main site q7v Corp. Below that are sub corps and DBAs. q7v Corp stands for Quick 7 Venture Corp. q7v Offers IT manages services, 24x7 support, Monitoring NOC, Remote Hands, Onsite support services. We have acquired TKLS, Inc, B & J Construction, BrightwallFix.com. We plan to acquire/spin up many companies that offer service, support and installation offerings and will all be known as an q7v Corp Company for branding purposes. We recently had our logo done, but then ran it through 3d glass as we like the look better than the original works. We have original files in vector, but not the 3D galss door render.

Target Market(s)

IT Server and Desktop Support. Construction. Mold Remediation. Mergers and Acquisitions.

Industry/Entity Type

It Company

Coding

Coded - Design and coding required

Font styles to use
Sans Serif

Colors
0792cd

Requirements
Must have
• Clean interface. Modern design. Mobile device and multi browser support. Must be for Wordpress. Job posting with resume submission module.Hook to our Web hosting portal (Tormund) API into VexaLine Reseller portal, customer portal to allow payments to their account etc.. Easy to edit. Easy to add to, Press Release Section, Investor Relations etc.
Should not have
• Slow loading. Played out design. Over use of stock images. Copied from a competitor or something point to such.

```html
<!DOCTYPE html>
<html lang="en">
<head>
<meta charset="utf-8">
<title>Q7V Corp</title>
<link href="https://fonts.googleapis.com/css2?family=Montserrat:wght@400;500;600;700&family=Open+Sans:wght@400;600&display=swap" rel="stylesheet">
<style>
:root{
  --brand:#0792cd;
  --brand-dark:#0a6fae;
  --ink:#333a40;
  --muted:#4a4f55;
  --topbar:#2c3238;
  --white:#ffffff;
}
*{box-sizing:border-box;margin:0;padding:0}
html,body{width:1200px;height:3502px;overflow:hidden}
body{position:relative;font-family:'Open Sans',sans-serif;color:var(--ink);background:var(--white)}
.abs{position:absolute}
.head{font-family:'Montserrat',sans-serif;font-weight:700;text-transform:uppercase}

/* header */
.topbar{left:0;top:0;width:1200px;height:89px;background:var(--topbar)}
.brand{left:93px;top:0;width:117px;height:89px;background:#3a4650;display:flex;align-items:center;justify-content:center;gap:6px}
.brand-name{font-family:'Montserrat',sans-serif;font-weight:700;font-size:26px;color:var(--white)}
.brand-dot{width:10px;height:10px;background:var(--brand)}
.contact-top{right:120px;top:32px;font-family:'Montserrat',sans-serif;font-size:16px;color:var(--white);display:flex;gap:34px}
.contact-top span{display:flex;align-items:center;gap:8px}
.nav{left:0;top:89px;width:1200px;height:58px;background:var(--brand)}
.nav ul{position:absolute;left:128px;top:0;height:58px;display:flex;align-items:center;gap:30px;list-style:none;font-family:'Montserrat',sans-serif;font-size:16px;color:var(--white)}
.quote{left:894px;top:89px;width:215px;height:58px;background:var(--brand-dark);color:var(--white);font-family:'Montserrat',sans-serif;font-size:17px;display:flex;align-items:center;justify-content:center;gap:10px}

/* hero */
.hero{left:0;top:147px;width:1200px;height:687px;background:linear-gradient(90deg,#15191c 0%,#3c4246 25%,#6d7275 50%,#3c4246 75%,#15191c 100%)}
.hero-shade{left:0;top:147px;width:1200px;height:687px;background:linear-gradient(180deg,rgba(0,0,0,.25),rgba(0,0,0,.1) 60%,rgba(0,0,0,.35))}
.hero-title{left:0;top:432px;width:1200px;text-align:center;font-size:52px;color:var(--white);letter-spacing:1px}
.hero-sub{left:300px;top:500px;width:600px;text-align:center;font-family:'Montserrat',sans-serif;font-weight:600;font-size:19px;line-height:36px;color:var(--white)}
.btn{display:flex;align-items:center;justify-content:center;gap:8px;background:var(--brand);color:var(--white);font-family:'Montserrat',sans-serif;font-weight:600;font-size:19px;border-radius:28px}
.social-side{left:44px;top:358px;width:18px;display:flex;flex-direction:column;gap:26px}
.follow{left:42px;top:640px;transform:rotate(-90deg);transform-origin:left top;color:var(--white);font-size:14px;font-family:'Montserrat',sans-serif}
.dot{width:12px;height:12px;border-radius:50%;background:var(--white)}

/* story */
.story-img{left:89px;top:918px;width:495px;height:327px;background:linear-gradient(135deg,#6b4a2a,#c99a5c 45%,#3a2e24)}
.section-title{font-size:32px;color:var(--brand-dark)}
.story-text{left:614px;top:978px;width:486px;font-size:15.5px;line-height:31px;color:var(--ink);text-align:justify}

/* services */
.services{left:0;top:1331px;width:1200px;height:490px;background:linear-gradient(180deg,#e6e8ea,#f3f4f5 50%,#e1e3e5)}
.svc{width:330px;text-align:center}
.svc-icon{width:146px;height:146px;border-radius:50%;background:var(--brand);margin:0 auto;display:flex;align-items:center;justify-content:center}
.svc h3{margin-top:28px;font-size:21px;color:var(--brand)}
.svc p{width:270px;margin:10px auto 0;font-size:16px;line-height:31px;color:var(--muted)}
.arrow{width:34px;height:34px;border:2px solid var(--brand);border-radius:50%;display:flex;align-items:center;justify-content:center}

/* blog */
.post{width:328px}
.post-img{height:194px;position:relative}
.date{position:absolute;left:17px;bottom:-14px;background:var(--brand);color:var(--white);font-size:13px;padding:6px 10px}
.post h4{margin-top:38px;font-size:17px;color:var(--brand)}
.post p{margin-top:10px;font-size:12.5px;line-height:24px;color:var(--ink)}
.read{margin-top:10px;font-family:'Montserrat',sans-serif;font-weight:700;font-size:13px;color:var(--brand)}

/* contact */
.contact{left:0;top:2405px;width:1200px;height:752px;background:linear-gradient(180deg,#d9dcdf,#eceef0 40%,#d4d7da)}
.contact-img{left:544px;top:2618px;width:574px;height:464px;background:linear-gradient(135deg,#4a4038,#b58a5c 50%,#c0562a 80%,#5a4a3c)}
.card{left:82px;top:2650px;width:530px;height:402px;background:var(--white);box-shadow:0 4px 20px rgba(0,0,0,.12)}
.field{position:absolute;border:2px solid #dcdfe2;font-size:12px;color:#6a6f74;padding:10px 14px;box-shadow:0 2px 4px rgba(0,0,0,.08)}

/* footer */
.footer{left:0;top:3157px;width:1200px;height:345px;background:var(--brand)}
.foot-brand{left:0;top:3206px;width:1200px;display:flex;justify-content:center;align-items:center;gap:12px}
.foot-brand-name{font-family:'Montserrat',sans-serif;font-weight:700;font-size:44px;line-height:60px;color:var(--white)}
.foot-brand-dot{width:14px;height:14px;background:var(--white)}
.foot-info{left:0;top:3304px;width:1200px;display:flex;justify-content:center;gap:40px;font-family:'Montserrat',sans-serif;font-size:16px;color:var(--white)}
.foot-info span{display:flex;align-items:center;gap:8px}
.foot-social{left:486px;top:3351px;display:flex;gap:11px}
.foot-social span{width:46px;height:46px;border-radius:50%;border:2px solid var(--white);display:flex;align-items:center;justify-content:center}
.foot-links{left:0;top:3420px;width:1200px;text-align:center;font-family:'Montserrat',sans-serif;font-weight:600;font-size:16px;color:var(--white)}
.copy{left:0;top:3469px;width:1200px;text-align:center;font-size:15px;color:var(--white)}
</style>
</head>
<body>

<header>
  <div class="abs topbar"></div>
  <div class="abs brand"><span class="brand-dot"></span><span class="brand-name">Q7V</span></div>
  <div class="abs contact-top">
    <span><svg width="16" height="16" viewBox="0 0 24 24" fill="#fff"><path d="M6.6 10.8a15 15 0 006.6 6.6l2.2-2.2c.3-.3.7-.4 1-.2 1.1.4 2.3.6 3.6.6.6 0 1 .4 1 1V20c0 .6-.4 1-1 1A17 17 0 013 4c0-.6.4-1 1-1h3.5c.6 0 1 .4 1 1 0 1.3.2 2.5.6 3.6.1.3 0 .7-.2 1z"/></svg>Call: 555 014 2270</span>
    <span><svg width="16" height="14" viewBox="0 0 24 20" fill="#fff"><path d="M2 2h20v16H2z M2 2l10 8 10-8" stroke="#2c3238" stroke-width="2"/></svg>Email: info@q7vcorp.com</span>
  </div>
  <nav class="abs nav">
    <ul><li>Home</li><li>About Us</li><li>Our Services</li><li>Our Companies ▾</li><li>Contact us</li></ul>
  </nav>
  <div class="abs quote"><svg width="18" height="18" viewBox="0 0 24 24" fill="#fff"><path d="M22 2L2 10l8 3 3 9z"/></svg>Get a Quote</div>
</header>

<section>
  <div class="abs hero" role="img" aria-label="Server room corridor with rows of racks"></div>
  <div class="abs hero-shade"></div>
  <svg class="abs" style="left:577px;top:376px" width="46" height="46" viewBox="0 0 46 46"><circle cx="23" cy="23" r="21" fill="none" stroke="#fff" stroke-width="2"/><path d="M18 14l13 9-13 9z" fill="none" stroke="#fff" stroke-width="2"/></svg>
  <h1 class="abs head hero-title">Q7V Corp</h1>
  <p class="abs hero-sub">Sed ut perspiciatis unde omnis iste natus error sit voluptatem accusantium doloremque</p>
  <div class="abs btn" style="left:392px;top:595px;width:213px;height:54px">
    <svg width="20" height="14" viewBox="0 0 24 16" fill="#fff"><path d="M12 0C6 0 1.7 4 0 8c1.7 4 6 8 12 8s10.3-4 12-8C22.3 4 18 0 12 0zm0 13a5 5 0 110-10 5 5 0 010 10z"/></svg>View More</div>
  <div class="abs btn" style="left:621px;top:595px;width:187px;height:54px">
    <svg width="18" height="18" viewBox="0 0 24 24" fill="#fff"><path d="M22 2L2 10l8 3 3 9z"/></svg>Contact us</div>
  <div class="abs social-side" aria-label="Social links">
    <svg width="16" height="16" viewBox="0 0 24 24" fill="none" stroke="#fff" stroke-width="2.5"><path d="M10 14a5 5 0 007 0l3-3a5 5 0 00-7-7l-1 1M14 10a5 5 0 00-7 0l-3 3a5 5 0 007 7l1-1"/></svg>
    <svg width="16" height="16" viewBox="0 0 24 24" fill="#fff"><circle cx="18" cy="5" r="3"/><circle cx="6" cy="12" r="3"/><circle cx="18" cy="19" r="3"/><path d="M8 11l8-5M8 13l8 5" stroke="#fff" stroke-width="2"/></svg>
    <svg width="16" height="16" viewBox="0 0 24 24" fill="none" stroke="#fff" stroke-width="2.5"><path d="M3 4h18v12H9l-5 4V4z"/></svg>
    <svg width="16" height="16" viewBox="0 0 24 24" fill="none" stroke="#fff" stroke-width="2.5"><circle cx="12" cy="12" r="9"/><path d="M3 12h18M12 3c3 3 3 15 0 18M12 3c-3 3-3 15 0 18"/></svg>
  </div>
  <div class="abs follow">Follow us</div>
  <div class="abs dot" style="left:1147px;top:468px"></div>
  <svg class="abs" style="left:1140px;top:498px" width="26" height="26"><circle cx="13" cy="13" r="11" fill="none" stroke="#fff" stroke-width="2"/><circle cx="13" cy="13" r="6" fill="#fff"/></svg>
  <div class="abs dot" style="left:1147px;top:543px"></div>
</section>

<section>
  <div class="abs story-img" role="img" aria-label="Hard hat, blueprints and tools on a workbench"></div>
  <svg class="abs" style="left:310px;top:1058px" width="46" height="46"><circle cx="23" cy="23" r="21" fill="none" stroke="#fff" stroke-width="2"/><path d="M18 14l13 9-13 9z" fill="none" stroke="#fff" stroke-width="2"/></svg>
  <h2 class="abs head section-title" style="left:614px;top:920px">Our Story</h2>
  <p class="abs story-text">q7v Corp is a Calverin and Tallowbine IT Solution Provider. We provide support for Desktops, Laptops, Tablets, Mobile Devices, Networking, WiFi, Server, Design and more by providing Remote and OnSite Support Services.<br>q7v Corp (Quick 7 Venture) Full service one stop shop service provider.</p>
  <div class="abs btn" style="left:614px;top:1181px;width:213px;height:54px">
    <svg width="20" height="14" viewBox="0 0 24 16" fill="#fff"><path d="M12 0C6 0 1.7 4 0 8c1.7 4 6 8 12 8s10.3-4 12-8C22.3 4 18 0 12 0zm0 13a5 5 0 110-10 5 5 0 010 10z"/></svg>View More</div>
</section>

<section>
  <div class="abs services" role="img" aria-label="Faded photo of plumbing tools in a workshop"></div>
  <h2 class="abs head section-title" style="left:0;top:1388px;width:1200px;text-align:center;color:var(--brand)">Our Services</h2>
  <div class="abs arrow" style="left:32px;top:1631px"><svg width="12" height="14"><path d="M9 2L3 7l6 5" fill="none" stroke="#0792cd" stroke-width="2"/></svg></div>
  <div class="abs arrow" style="left:1129px;top:1631px"><svg width="12" height="14"><path d="M3 2l6 5-6 5" fill="none" stroke="#0792cd" stroke-width="2"/></svg></div>
  <div class="abs svc" style="left:94px;top:1470px">
    <div class="svc-icon"><svg width="70" height="60" viewBox="0 0 70 60" fill="none" stroke="#fff" stroke-width="3"><path d="M18 28a10 10 0 0 1 4-18 14 14 0 0 1 27 2 10 10 0 0 1 3 16z"/><rect x="16" y="34" width="38" height="8"/><rect x="16" y="46" width="38" height="8"/></svg></div>
    <h3 class="head">Cloud / Hosting</h3>
    <p>Sed ut perspiciatis unde omnis iste natus error sit voluptatem accutium doloremque</p>
  </div>
  <div class="abs svc" style="left:435px;top:1470px">
    <div class="svc-icon"><svg width="64" height="64" viewBox="0 0 64 64" fill="none" stroke="#fff" stroke-width="3"><circle cx="32" cy="26" r="14"/><circle cx="32" cy="26" r="5"/><path d="M32 6v6M32 40v6M12 26h6M46 26h6M20 54h24"/></svg></div>
    <h3 class="head">Commercial Services</h3>
    <p>Sed ut perspiciatis unde omnis iste natus error sit voluptatem accutium doloremque</p>
  </div>
  <div class="abs svc" style="left:774px;top:1470px">
    <div class="svc-icon"><svg width="60" height="64" viewBox="0 0 60 64" fill="none" stroke="#fff" stroke-width="3"><rect x="8" y="18" width="20" height="40"/><rect x="28" y="6" width="24" height="52"/><path d="M34 14h4M42 14h4M34 24h4M42 24h4M34 34h4M42 34h4M14 28h8M14 38h8"/></svg></div>
    <h3 class="head">Construction</h3>
    <p>Sed ut perspiciatis unde omnis iste natus error sit voluptatem accutium doloremque</p>
  </div>
</section>

<section>
  <h2 class="abs head section-title" style="left:0;top:1883px;width:1200px;text-align:center">Our Blog</h2>
  <article class="abs post" style="left:77px;top:1954px">
    <div class="post-img" role="img" aria-label="Blue-lit data center aisle" style="background:linear-gradient(180deg,#0d1d3a,#2d5fa8 50%,#0a1628)"><span class="date">▦ Oct 27 2018</span></div>
    <h4 class="head">Sed ut perspiciatis und</h4>
    <p>Sed ut perspiciatis unde omnis iste natus error sit voluptatem accusantium doloremque laudantium, totam rem aperiam, eaque ipsa quae ab illo</p>
    <div class="read">READ MORE</div>
  </article>
  <article class="abs post" style="left:437px;top:1954px">
    <div class="post-img" role="img" aria-label="Hands sketching plans beside a laptop" style="background:linear-gradient(135deg,#8a8680,#d8d2c6 50%,#6e6a64)"><span class="date">▦ Oct 27 2018</span></div>
    <h4 class="head">Sed ut perspiciatis und</h4>
    <p>Sed ut perspiciatis unde omnis iste natus error sit voluptatem accusantium doloremque laudantium, totam rem aperiam, eaque ipsa quae ab illo</p>
    <div class="read">READ MORE</div>
  </article>
  <article class="abs post" style="left:794px;top:1954px">
    <div class="post-img" role="img" aria-label="Technician in overalls with a clipboard" style="background:linear-gradient(135deg,#d9dcde,#6f7f95 50%,#e4e6e8)"><span class="date">▦ Oct 27 2018</span></div>
    <h4 class="head">Sed ut perspiciatis und</h4>
    <p>Sed ut perspiciatis unde omnis iste natus error sit voluptatem accusantium doloremque laudantium, totam rem aperiam, eaque ipsa quae ab illo</p>
    <div class="read">READ MORE</div>
  </article>
</section>

<section>
  <div class="abs contact" role="img" aria-label="Faded server room background"></div>
  <h2 class="abs head section-title" style="left:0;top:2468px;width:1200px;text-align:center">Contact Us</h2>
  <p class="abs" style="left:250px;top:2522px;width:700px;text-align:center;font-size:15.5px;line-height:32px;color:var(--muted)">At vero eos et accusamus et iusto odio dignissimos ducimus qui blanditiis praesentium voluptatum deleniti atque corrupti quos dolores et</p>
  <div class="abs contact-img" role="img" aria-label="Engineers reviewing plans with a hard hat on the desk"></div>
  <form class="abs card">
    <h3 class="head" style="position:absolute;left:42px;top:38px;font-size:25px;color:var(--brand-dark)">Get in Touch</h3>
    <div class="field" style="left:42px;top:89px;width:217px;height:47px">Name</div>
    <div class="field" style="left:275px;top:89px;width:215px;height:47px">Email</div>
    <div class="field" style="left:42px;top:152px;width:217px;height:49px">Phone Number</div>
    <div class="field" style="left:275px;top:152px;width:215px;height:49px">Subject</div>
    <div class="field" style="left:42px;top:215px;width:448px;height:91px">Message</div>
    <div class="btn" style="position:absolute;left:42px;top:327px;width:140px;height:42px;font-size:17px">Submit</div>
  </form>
</section>

<footer>
  <div class="abs footer"></div>
  <div class="abs foot-brand"><span class="foot-brand-dot"></span><span class="foot-brand-name">Q7V Corp</span></div>
  <div class="abs foot-info">
    <span><svg width="16" height="16" viewBox="0 0 24 24" fill="#fff"><path d="M22 2L2 10l8 3 3 9z"/></svg>212 Harlow Avenue Brookfield</span>
    <span><svg width="16" height="16" viewBox="0 0 24 24" fill="#fff"><path d="M6.6 10.8a15 15 0 006.6 6.6l2.2-2.2c.3-.3.7-.4 1-.2 1.1.4 2.3.6 3.6.6.6 0 1 .4 1 1V20c0 .6-.4 1-1 1A17 17 0 013 4c0-.6.4-1 1-1h3.5c.6 0 1 .4 1 1 0 1.3.2 2.5.6 3.6.1.3 0 .7-.2 1z"/></svg>Phone: +(555) 014-2270</span>
    <span><svg width="16" height="14" viewBox="0 0 24 20" fill="#fff"><path d="M2 2h20v16H2z M2 2l10 8 10-8" stroke="#0792cd" stroke-width="2"/></svg>Email: info@q7vcorp.com</span>
  </div>
  <div class="abs foot-social" aria-label="Social links">
    <span><svg width="20" height="20" viewBox="0 0 24 24" fill="none" stroke="#fff" stroke-width="2.5"><path d="M10 14a5 5 0 007 0l3-3a5 5 0 00-7-7l-1 1M14 10a5 5 0 00-7 0l-3 3a5 5 0 007 7l1-1"/></svg></span>
    <span><svg width="20" height="20" viewBox="0 0 24 24" fill="#fff"><circle cx="18" cy="5" r="3"/><circle cx="6" cy="12" r="3"/><circle cx="18" cy="19" r="3"/><path d="M8 11l8-5M8 13l8 5" stroke="#fff" stroke-width="2"/></svg></span>
    <span><svg width="20" height="20" viewBox="0 0 24 24" fill="none" stroke="#fff" stroke-width="2.5"><path d="M3 4h18v12H9l-5 4V4z"/></svg></span>
    <span><svg width="20" height="20" viewBox="0 0 24 24" fill="none" stroke="#fff" stroke-width="2.5"><circle cx="12" cy="12" r="9"/><path d="M3 12h18M12 3c3 3 3 15 0 18M12 3c-3 3-3 15 0 18"/></svg></span>
    <span><svg width="20" height="20" viewBox="0 0 24 24" fill="none" stroke="#fff" stroke-width="2.5"><path d="M3 5h18v14H3z M3 5l9 7 9-7"/></svg></span>
  </div>
  <div class="abs foot-links">Home &nbsp;|&nbsp; About Us &nbsp;|&nbsp; Our Service &nbsp;|&nbsp; Our Companies &nbsp;|&nbsp; Our Blog &nbsp;|&nbsp; Contact us</div>
  <div class="abs copy">Copyright © 2018. All Rights Reserved.</div>
</footer>

</body>
</html>
```